Logo, Web and Mobile Designs for enterprise social media platform

All the details are in the attached document, please start reading the scope document first which explains what is this project about and the details about the needed deliverables, after that please read the UI_Requirements document which will detail what is expected regarding the coded web version since this is a coded contest, it is very important that you meet the UI requirements or suggest something else but we will need to agree first before working on the coded version

Good Luck

Target Market(s)

Enterprise Social Media

Industry/Entity Type

Media

Coding

Coded - Design and coding required

Number of Pages Required

5+ page

Font styles to use
Sans Serif

Requirements
Must have
• All the must haves are listed in the scope document so please check before you start

```html
<!DOCTYPE html>
<html lang="en">
<head>
<meta charset="utf-8">
<title>Teamora – Event Members</title>
<link href="https://fonts.googleapis.com/css2?family=Roboto:wght@300;400;500&display=swap" rel="stylesheet">
<style>
:root{
  --brand:#1e8ab8;
  --accent:#1997c6;
  --orange:#f39c12;
  --page:#ebebeb;
  --header:#f8f8f8;
  --side:#f3f3f3;
  --content:#fafafa;
  --line:#e2e2e2;
  --text:#555;
  --muted:#777;
}
*{box-sizing:border-box;margin:0;padding:0}
html,body{width:1200px;height:826px;overflow:hidden}
body{font-family:"Roboto",sans-serif;background:var(--page);color:var(--text);position:relative}
.topbar{position:absolute;left:0;top:0;width:1200px;height:70px;background:var(--header);border-bottom:1px solid #ddd}
.menu-btn{position:absolute;left:0;top:0;width:145px;height:70px;border-right:1px solid #e8e8e8}
.menu-btn svg{position:absolute;left:100px;top:28px}
.brand{position:absolute;left:168px;top:14px;display:flex;align-items:center;gap:8px}
.brand-dot{width:42px;height:42px;border-radius:50%;background:var(--orange)}
.brand-name{font-size:31px;font-weight:500;color:var(--brand);letter-spacing:.5px}
.user{position:absolute;left:746px;top:19px;display:flex;align-items:center;gap:10px}
.avatar{width:34px;height:34px;border-radius:50%;background:linear-gradient(135deg,#6b6b6b,#2e2e2e)}
.user-name{font-size:16px;color:#555;font-weight:400}
.caret{margin-left:6px}
.tool{position:absolute;top:0;height:70px;border-left:1px solid #e8e8e8}
.tool svg{position:absolute}
.badge{position:absolute;top:16px;min-width:20px;height:16px;border-radius:8px;font-size:11px;color:#fff;text-align:center;line-height:16px}
.badge.orange{background:var(--orange)}
.badge.blue{background:var(--accent)}
.card{position:absolute;left:99px;top:105px;width:1001px;height:534px;background:var(--content);border:1px solid #dadada}
.sidebar{position:absolute;left:0;top:0;width:278px;height:532px;background:var(--side);border-right:2px solid #e4e4e4}
.side-head{height:56px;display:flex;align-items:center;padding-left:18px;gap:14px;font-size:15.5px;color:#444;border-bottom:1px solid var(--line)}
.side-list{list-style:none;margin-top:16px}
.side-list li{height:32.6px;display:flex;align-items:center;padding-left:18px;gap:14px;font-size:15.5px;color:#666;border-bottom:1px solid var(--line)}
.side-list li.active{color:var(--accent);font-weight:500}
.panel{position:absolute;left:311px;top:41px;width:659px;height:240px;background:#fff;border:1px solid #e8e8e8}
.panel-head{height:49px;background:#f4f5f7;border-bottom:1px solid #e3e3e3;display:flex;align-items:center;padding-left:20px;gap:8px;font-size:15.5px;color:#555}
.row{position:absolute;left:22px;display:flex;align-items:center}
.row label{width:164px;font-size:14.5px;color:#666}
.chip{width:300px;height:38px;border:1px solid #e2e2e2;background:#fff;display:flex;align-items:center;padding:0 6px 0 10px;gap:7px}
.chip-pic{width:21px;height:21px;background:#b8a593}
.chip-name{flex:1;font-size:12px;color:#444}
.chip-remove{width:22px;height:22px;background:var(--accent);color:#fff;font-size:14px;line-height:20px;text-align:center}
.footer{position:absolute;left:0;top:679px;width:1200px;height:147px;background:var(--brand);color:#fff;text-align:center}
.social{display:flex;justify-content:center;gap:13px;margin-top:29px}
.social span{width:24px;height:24px;border-radius:4px;background:#fff}
.links{margin-top:16px;font-size:14.5px;color:#eaf5fb}
.links em{font-style:normal;margin:0 9px}
.copy{margin-top:12px;font-size:14.5px}
</style>
</head>
<body>
<header class="topbar">
  <div class="menu-btn"><svg width="20" height="16"><rect y="0" width="20" height="3" fill="#777"/><rect y="6" width="20" height="3" fill="#777"/><rect y="12" width="20" height="3" fill="#777"/></svg></div>
  <div class="brand"><span class="brand-dot"></span><span class="brand-name">Teamora</span></div>
  <div class="user"><div class="avatar" role="img" aria-label="User profile photo"></div><span class="user-name">Mark Dalton</span>
    <svg class="caret" width="12" height="7"><path d="M0 0h12L6 7z" fill="#555"/></svg></div>
  <div class="tool" style="left:922px;width:69px">
    <svg style="left:24px;top:26px" width="20" height="19"><rect width="9" height="5" fill="#666"/><rect y="7" width="20" height="5" fill="#666"/><rect y="14" width="12" height="5" fill="#666"/></svg>
    <span class="badge orange" style="left:36px">8</span></div>
  <div class="tool" style="left:991px;width:60px">
    <svg style="left:20px;top:25px" width="20" height="20"><circle cx="8" cy="8" r="6" stroke="#666" stroke-width="2.5" fill="none"/><path d="M12.5 12.5L18 18" stroke="#666" stroke-width="3" stroke-linecap="round"/></svg></div>
  <div class="tool" style="left:1051px;width:149px">
    <svg style="left:21px;top:26px" width="20" height="20"><path d="M10 1c-4 0-6 3-6 7v5l-2 3h16l-2-3V8c0-4-2-7-6-7z" fill="#666"/><circle cx="10" cy="18" r="2" fill="#666"/></svg>
    <span class="badge blue" style="left:28px">8</span></div>
</header>

<main class="card">
  <nav class="sidebar">
    <div class="side-head"><svg width="15" height="13"><rect width="7" height="6" fill="#1997c6"/><rect x="8" width="7" height="6" fill="#1997c6"/><rect y="7" width="7" height="6" fill="#1997c6"/><rect x="8" y="7" width="7" height="6" fill="#1997c6"/></svg>VIEW DASHBOARD</div>
    <div class="side-head"><svg width="15" height="15"><rect y="2" width="15" height="13" fill="none" stroke="#1997c6" stroke-width="2"/><rect y="2" width="15" height="4" fill="#1997c6"/><rect x="3" width="2" height="4" fill="#1997c6"/><rect x="10" width="2" height="4" fill="#1997c6"/></svg>VIEW EVENT</div>
    <ul class="side-list">
      <li><svg width="6" height="10"><path d="M1 1l4 4-4 4" stroke="#666" fill="none" stroke-width="1.5"/></svg>About Us</li>
      <li><svg width="6" height="10"><path d="M1 1l4 4-4 4" stroke="#666" fill="none" stroke-width="1.5"/></svg>Speakers</li>
      <li><svg width="6" height="10"><path d="M1 1l4 4-4 4" stroke="#666" fill="none" stroke-width="1.5"/></svg>Track</li>
      <li><svg width="6" height="10"><path d="M1 1l4 4-4 4" stroke="#666" fill="none" stroke-width="1.5"/></svg>Sessions</li>
      <li><svg width="6" height="10"><path d="M1 1l4 4-4 4" stroke="#666" fill="none" stroke-width="1.5"/></svg>Tickets</li>
      <li><svg width="6" height="10"><path d="M1 1l4 4-4 4" stroke="#666" fill="none" stroke-width="1.5"/></svg>Organizers</li>
      <li><svg width="6" height="10"><path d="M1 1l4 4-4 4" stroke="#666" fill="none" stroke-width="1.5"/></svg>Sponsors</li>
      <li><svg width="6" height="10"><path d="M1 1l4 4-4 4" stroke="#666" fill="none" stroke-width="1.5"/></svg>Exhibitor</li>
      <li><svg width="6" height="10"><path d="M1 1l4 4-4 4" stroke="#666" fill="none" stroke-width="1.5"/></svg>Security</li>
      <li class="active"><svg width="6" height="10"><path d="M1 1l4 4-4 4" stroke="#666" fill="none" stroke-width="1.5"/></svg>MEMBERS</li>
    </ul>
  </nav>

  <section class="panel">
    <div class="panel-head"><svg width="14" height="14"><rect y="2" width="14" height="12" fill="none" stroke="#666" stroke-width="1.5"/><rect y="2" width="14" height="3" fill="#666"/><path d="M0 8h14M0 11h14M4 5v9M7 5v9M10 5v9" stroke="#666" stroke-width="1"/></svg>EVENT MEMBERS</div>
    <div class="row" style="top:89px"><label>Members :</label>
      <div class="chip"><span class="chip-pic" role="img" aria-label="Member photo"></span><span class="chip-name">kmoreno.lee</span><span class="chip-remove">–</span></div></div>
    <div class="row" style="top:146px"><label>Administrators :</label>
      <div class="chip"><span class="chip-pic" role="img" aria-label="Administrator photo"></span><span class="chip-name">kmoreno.lee</span><span class="chip-remove">–</span></div></div>
  </section>
</main>

<footer class="footer">
  <div class="social"><span></span><span></span><span></span><span></span><span></span></div>
  <div class="links">Home<em>/</em>Contact<em>/</em>Topics<em>/</em>Posts and Comments<em>/</em>Discussion<em>/</em>Videos Links</div>
  <div class="copy">Copyright @ 2015 - 2015.Teamora. All Rights Reserved.</div>
</footer>
</body>
</html>
```